Marlowe Group needs a business card

I would like the card to be simple but modern and elegant.
I like black and white.
or black and gold.
we are a private finance lender and also are involved in property and property developments.

please look at the business card photos i provided i would like M.G only one one side and all the other details on the other side use fonts that tie in with my theme.

Industry/Entity Type

Finance

Contact Information for Business Card

Marlowe Group (M.G) Daniel Marlowe M: 0413586207 E: danmarl@inboxmail.test

Font styles to use
Other font styles liked:
• Use fonts that would reflect our business

Colors
000000
ffffff

Requirements
Must have
• one side of details
• other side has either M.G or Marlowe Group like in the photos provided

```html
<!DOCTYPE html>
<html lang="en">
<head>
<meta charset="UTF-8">
<title>Marlowe Group — Business Card</title>
<link href="https://fonts.googleapis.com/css2?family=Raleway:wght@400;500;600&display=swap" rel="stylesheet">
<style>
  :root {
    --backdrop: #5a5a5a;
    --card: #ebebea;
    --ink: #4a4a4a;
    --ink-soft: #5c5c5c;
    --rule: #3a3a3a;
  }
  * { box-sizing: border-box; margin: 0; padding: 0; }
  html, body {
    width: 1200px;
    height: 1000px;
    overflow: hidden;
  }
  body {
    background: var(--backdrop);
    font-family: "Raleway", sans-serif;
    display: flex;
    flex-direction: column;
    align-items: center;
    justify-content: center;
    gap: 44px;
  }
  .card {
    width: 700px;
    height: 400px;
    background: var(--card);
    box-shadow: 0 6px 18px rgba(0,0,0,0.35);
    position: relative;
  }
  .card-front {
    display: flex;
    align-items: center;
    justify-content: center;
  }
  .company-name {
    font-size: 52px;
    font-weight: 500;
    color: var(--ink);
    letter-spacing: 0.5px;
  }
  .card-back .details {
    position: absolute;
    left: 0;
    right: 0;
    top: 268px;
  }
  .name-row {
    display: flex;
    align-items: center;
    gap: 18px;
  }
  .name-row .rule {
    flex: 1;
    height: 1px;
    background: var(--rule);
  }
  .person-name {
    font-size: 21px;
    font-weight: 600;
    letter-spacing: 1.6px;
    color: var(--ink);
    text-transform: uppercase;
  }
  .contact {
    margin-top: 18px;
    text-align: center;
    font-size: 17px;
    font-weight: 400;
    letter-spacing: 1.4px;
    color: var(--ink-soft);
  }
</style>
</head>
<body>
  <section class="card card-front">
    <h1 class="company-name">Marlowe Group</h1>
  </section>

  <section class="card card-back">
    <div class="details">
      <div class="name-row">
        <span class="rule"></span>
        <h2 class="person-name">Daniel Marlowe</h2>
        <span class="rule"></span>
      </div>
      <p class="contact">M: 0413586207 | E: danmarl@inboxmail.test</p>
    </div>
  </section>
</body>
</html>
```